Vantro cards

I am in the auto motive, transportation business I would like a business card that is Something cool, modern edgy, having to do with car culture. I offer towing service for high and exotic cars. I also provide towing for collisions and car accidents. I offer open and enclosed transport nationwide.

Target Market(s)

Car culture people high end auto collectors

Industry/Entity Type

Towing car carrier

Contact Information for Business Card

My company colors black yellow and silver

Font styles to use
Serif

```html
<!DOCTYPE html>
<html lang="en">
<head>
<meta charset="utf-8">
<title>Vantro Business Cards</title>
<link rel="stylesheet" href="https://fonts.googleapis.com/css2?family=Poppins:wght@300;400;600;700&display=swap">
<style>
  :root {
    --bg: #2a2624;
    --card-back: #050505;
    --card-front: #1c1c1c;
    --yellow: #f9dc5c;
    --white: #ffffff;
    --silver: #d9d9d9;
  }
  * { margin: 0; padding: 0; box-sizing: border-box; }
  html, body {
    width: 1200px;
    height: 842px;
    overflow: hidden;
    background: var(--bg);
    font-family: "Poppins", sans-serif;
  }
  .stage {
    position: relative;
    width: 1200px;
    height: 842px;
  }
  .card {
    position: absolute;
    top: 272px;
    width: 520px;
    height: 298px;
    overflow: hidden;
    box-shadow: 0 10px 28px rgba(0,0,0,0.55);
  }

  /* Contact side */
  .card--contact {
    left: 60px;
    background: var(--card-back);
  }
  .band {
    position: absolute;
    left: 0;
    width: 100%;
    height: 11px;
    background: var(--yellow);
  }
  .band--top { top: 14px; }
  .band--bottom { bottom: 14px; }
  .contact {
    position: absolute;
    top: 62px;
    left: 0;
    width: 100%;
    text-align: center;
    color: var(--silver);
    text-transform: uppercase;
  }
  .contact__name {
    font-weight: 700;
    font-size: 19px;
    color: var(--yellow);
    letter-spacing: 0.5px;
    line-height: 1.1;
  }
  .contact__title {
    font-weight: 400;
    font-size: 12px;
    letter-spacing: 0.6px;
    color: var(--white);
  }
  .divider {
    width: 56px;
    height: 1.5px;
    background: var(--yellow);
    margin: 10px auto;
  }
  .contact__line {
    font-weight: 300;
    font-size: 12.5px;
    line-height: 1.35;
    letter-spacing: 0.4px;
    color: var(--white);
  }
  .contact__line--phone { font-size: 14px; font-weight: 400; }
  .contact__address { margin-top: 16px; }

  /* Brand side */
  .card--brand {
    left: 620px;
    background: var(--card-front);
  }
  .accent {
    position: absolute;
    display: flex;
  }
  .accent__block {
    width: 26px;
    height: 58px;
    background: var(--yellow);
  }
  .accent__stripe {
    width: 4px;
    height: 58px;
    background: var(--white);
    margin: 0 5px;
  }
  .accent--left { left: 0; top: 168px; }
  .accent--right { right: 0; top: 58px; flex-direction: row-reverse; }
  .brand {
    position: absolute;
    top: 50%;
    left: 50%;
    transform: translate(-50%, -50%);
    display: flex;
    align-items: center;
    gap: 14px;
  }
  .brand__mark {
    width: 22px;
    height: 22px;
    background: var(--yellow);
  }
  .brand__name {
    font-weight: 700;
    font-size: 52px;
    letter-spacing: 2px;
    color: var(--white);
    text-transform: uppercase;
  }
</style>
</head>
<body>
  <main class="stage">
    <section class="card card--contact">
      <div class="band band--top"></div>
      <div class="contact">
        <p class="contact__name">Marcus Hale</p>
        <p class="contact__title">Managing Director</p>
        <div class="divider"></div>
        <p class="contact__line contact__line--phone">044-318 662 401</p>
        <p class="contact__line">hello@vantrohaul.com</p>
        <p class="contact__line">www.vantrohaul.com</p>
        <div class="divider"></div>
        <p class="contact__line">218, Ridgeway Motor Lane</p>
        <p class="contact__line">60614, United States</p>
      </div>
      <div class="band band--bottom"></div>
    </section>

    <section class="card card--brand">
      <div class="accent accent--left">
        <div class="accent__block"></div>
        <div class="accent__stripe"></div>
      </div>
      <div class="accent accent--right">
        <div class="accent__block"></div>
        <div class="accent__stripe"></div>
      </div>
      <div class="brand">
        <span class="brand__mark"></span>
        <span class="brand__name">Vantro</span>
      </div>
    </section>
  </main>
</body>
</html>
```